brightwell - Property Management DL Card

I am after a savvy designer to cut through junk mail! so many real estate agents use flyers to promote themselves and their business and usually sales. We are a property management firm (residential) and we want to represent landlords that have existing investment properties and need a quality agent to represent them. Can you help?
DL size, will be printed and delivered to mailboxes. For a look at our website go to www.brightwellrs.com.au. Keep it simple and clutter free.
it is to be double sided - with one side to be simple and clear - just our website, logo and telephone number on the back.
attached is our logo and our telephone number is 1300 48 92 16
the above are 2 essential elements to be included + our email address: admin@brightwellrs.com.au
also attached are our transparent price list

Target Market(s)
property investors,
people that manage properties themselves
Industry/Entity Type
Property Management
- arial
Look and feel

```html
<!DOCTYPE html>
<html lang="en">
<head>
<meta charset="utf-8">
<title>brightwell – Property Management DL Card</title>
<link rel="stylesheet" href="https://fonts.googleapis.com/css2?family=Open+Sans:wght@400;600;700&display=swap">
<style>
  :root {
    --page-bg: #e6e6e6;
    --frame-stone: #c5bfb3;
    --back-stone: #b1aa99;
    --paper: #ffffff;
    --brand-red: #e0191d;
    --text-dark: #2b2b2b;
    --text-brown: #4a4034;
    --bullet-grey: #9b9b9b;
  }
  * { box-sizing: border-box; margin: 0; padding: 0; }
  html, body { width: 1200px; height: 1200px; overflow: hidden; }
  body {
    background: var(--page-bg);
    font-family: "Open Sans", Arial, sans-serif;
    position: relative;
  }
  .card { position: absolute; }

  /* Front side */
  .card-front {
    left: 120px; top: 55px; width: 1000px; height: 500px;
    background: var(--frame-stone);
  }
  .front-paper {
    position: absolute; left: 22px; top: 23px; width: 955px; height: 455px;
    background: var(--paper);
  }
  .hero-photo {
    position: absolute; left: 0; top: 23px; width: 667px; height: 477px;
    background: linear-gradient(180deg, #ecebea 0%, #d9d6d3 30%, #b93c3e 62%, #c42a2e 72%, #5b5656 88%, #3f3c3c 100%);
  }
  .headline-band {
    position: absolute; left: 435px; top: 115px; width: 535px; height: 28px;
    background: linear-gradient(90deg, rgba(224,25,29,0) 0%, var(--brand-red) 22%, var(--brand-red) 85%, rgba(224,25,29,0) 100%);
    color: #fff; font-weight: 600; font-size: 21px; line-height: 28px;
    padding-left: 102px; white-space: nowrap;
  }
  .benefit-list {
    position: absolute; left: 696px; top: 156px; list-style: none;
    font-size: 16.8px; color: var(--text-dark); line-height: 21.7px;
  }
  .benefit-list li { display: flex; align-items: center; gap: 6px; }
  .benefit-list svg { width: 10px; height: 10px; flex: none; }
  .front-name {
    position: absolute; left: 748px; top: 392px;
    font-size: 32px; font-weight: 600; line-height: 40px;
    color: var(--text-dark);
  }

  /* Back side */
  .card-back {
    left: 121px; top: 638px; width: 1001px; height: 500px;
    background: var(--back-stone);
  }
  .back-name {
    position: absolute; left: 137px; top: 62px;
    font-size: 32px; font-weight: 600; line-height: 40px;
    color: var(--text-brown);
  }
  .contact-block {
    position: absolute; left: 555px; top: 380px; height: 64px;
    border-left: 2px solid var(--text-brown);
    padding-left: 19px; color: var(--text-brown);
    font-size: 18.5px; letter-spacing: 0.3px;
  }
  .contact-block .line { line-height: 24px; height: 24px; white-space: nowrap; }
  .contact-block .call-label { font-size: 17px; }
  .contact-block .phone { font-weight: 700; font-size: 23px; line-height: 1; margin-left: 10px; letter-spacing: 0.8px; }
</style>
</head>
<body>
  <section class="card card-front" aria-label="Card front">
    <div class="front-paper"></div>
    <div class="hero-photo" role="img" aria-label="Photo of a modern open-plan living room with red sofas, white walls and a timber floor"></div>
    <div class="headline-band">Property Management specialists</div>
    <ul class="benefit-list">
      <li><svg viewBox="0 0 10 10"><path d="M5 0 10 5 5 10 0 5Z" fill="var(--bullet-grey)"/></svg>Excellent communication</li>
      <li><svg viewBox="0 0 10 10"><path d="M5 0 10 5 5 10 0 5Z" fill="var(--bullet-grey)"/></svg>No hidden extras</li>
      <li><svg viewBox="0 0 10 10"><path d="M5 0 10 5 5 10 0 5Z" fill="var(--bullet-grey)"/></svg>Minimal vacancy</li>
      <li><svg viewBox="0 0 10 10"><path d="M5 0 10 5 5 10 0 5Z" fill="var(--bullet-grey)"/></svg>The best rent return</li>
    </ul>
    <div class="front-name">brightwell</div>
  </section>

  <section class="card card-back" aria-label="Card back">
    <div class="back-name">brightwell</div>
    <div class="contact-block">
      <div class="line"><span class="call-label">CALL TODAY!</span><span class="phone">1300 48 92 16</span></div>
      <div class="line">PO Box C302, Parramatta NSW, 2150</div>
      <div class="line">admin@brightwellrs.com.au</div>
    </div>
  </section>
</body>
</html>
```